I am looking for a modern, clean and neat design for a reflexology and well being business. The business name is Gralo Tund (this is an old Latin word for wellbeing). The colours I would like are purple, white and grey. I am open to suggestions for pictures such as healing or working hands, a pair of feet, images that represent my business that you may think of....... or maybe you think no images at all would be best? My tag line is: "Relax, Renew, Revive" or "Find you balance......... Relax, Renew, Revive" I can decide which I want so I would like to see what both would look like. I would like space on the back to write the client's appointment date and time (more than once)

```html
<!DOCTYPE html>
<html lang="en">
<head>
<meta charset="utf-8">
<title>Gralo Tund – Business Card</title>
<link rel="stylesheet" href="https://fonts.googleapis.com/css2?family=Open+Sans:wght@400;600;700&display=swap">
<style>
  :root {
    --stage: #e9e9ec;
    --charcoal: #4d4d4f;
    --lavender: #a3b8df;
    --white: #ffffff;
    --ink: #55575a;
    --dots: #d6d6d8;
  }
  * { box-sizing: border-box; margin: 0; padding: 0; }
  html, body { width: 1200px; height: 900px; overflow: hidden; }
  body {
    position: relative;
    background: var(--stage);
    font-family: "Open Sans", Arial, sans-serif;
  }
  .card {
    position: absolute;
    width: 660px;
    height: 380px;
    border-radius: 22px;
    overflow: hidden;
    box-shadow: 0 10px 28px rgba(0,0,0,.18);
  }

  /* Back of card */
  .card--back { left: 70px; top: 50px; background: var(--charcoal); color: var(--white); }
  .brand-block {
    position: absolute; right: 46px; top: 42px;
    display: flex; flex-direction: column; align-items: flex-end; gap: 14px;
  }
  .brand-name {
    display: flex; align-items: center; gap: 12px;
    font-size: 30px; font-weight: 400; letter-spacing: 2px;
    color: var(--lavender); text-transform: uppercase;
  }
  .brand-dot { width: 22px; height: 22px; border-radius: 50%; background: var(--lavender); }
  .tagline { font-size: 14px; font-weight: 600; letter-spacing: .5px; }
  .appointment { position: absolute; left: 48px; bottom: 40px; width: 420px; }
  .appointment h2 { font-size: 20px; font-weight: 700; margin-bottom: 12px; }
  .field { display: flex; align-items: baseline; font-size: 14px; margin: 10px 0 0 18px; }
  .field span { white-space: nowrap; }
  .field i { flex: 1; border-bottom: 2px dotted var(--dots); margin-left: 4px; }

  /* Front of card */
  .card--front { left: 470px; top: 470px; background: var(--white); }
  .panel-band {
    position: absolute; right: 0; top: 90px; bottom: 0; width: 270px;
    background: var(--charcoal);
    border-top-left-radius: 140px 290px;
  }
  .panel-contact {
    position: absolute; right: 0; top: 170px; bottom: 0; width: 196px;
    background: var(--lavender);
    border-top-left-radius: 48px;
  }
  .front-brand {
    position: absolute; left: 58px; top: 150px;
    display: flex; align-items: center; gap: 14px;
    font-size: 34px; font-weight: 400; letter-spacing: 2px;
    color: var(--ink); text-transform: uppercase;
  }
  .front-brand .brand-dot { width: 26px; height: 26px; }
  .contact { position: absolute; left: 488px; top: 202px; width: 160px; color: var(--white); }
  .contact__name { font-size: 20px; font-weight: 700; letter-spacing: .3px; text-transform: uppercase; line-height: 1; white-space: nowrap; }
  .contact__role { font-size: 12px; font-weight: 600; color: var(--ink); text-transform: uppercase; margin: 4px 0 14px; }
  .contact__line { display: flex; align-items: center; gap: 7px; font-size: 12.5px; line-height: 1.6; white-space: nowrap; }
  .contact__line svg { width: 10px; height: 10px; flex: none; }
</style>
</head>
<body>

<section class="card card--back">
  <div class="brand-block">
    <div class="brand-name"><span class="brand-dot"></span>Gralo Tund</div>
    <p class="tagline">RELAX, RENEW, REVIVE</p>
  </div>
  <div class="appointment">
    <h2>Appointment:</h2>
    <p class="field"><span>Name:</span><i></i></p>
    <p class="field"><span>Time:</span><i></i></p>
    <p class="field"><span>Date:</span><i></i></p>
  </div>
</section>

<section class="card card--front">
  <div class="panel-band" aria-hidden="true"></div>
  <div class="panel-contact" aria-hidden="true"></div>

  <div class="front-brand"><span class="brand-dot"></span>Gralo Tund</div>

  <div class="contact">
    <p class="contact__name">Mara Velden</p>
    <p class="contact__role">Director</p>
    <p class="contact__line">
      <svg viewBox="0 0 10 10"><path fill="var(--white)" d="M2 0.5 L3.6 2.6 L2.8 3.6 C3.4 5 4.8 6.4 6.3 7.2 L7.4 6.4 L9.5 8 L8.4 9.6 C4.5 9 1 5.5 0.4 1.6 Z"/></svg>
      +330 5512-0193
    </p>
    <p class="contact__line">
      <svg viewBox="0 0 10 10"><rect x="0.6" y="2" width="8.8" height="6" fill="none" stroke="var(--white)" stroke-width="1.2"/><path d="M0.8 2.3 L5 5.6 L9.2 2.3" fill="none" stroke="var(--white)" stroke-width="1.2"/></svg>
      info@gralotund.com
    </p>
    <p class="contact__line">
      <svg viewBox="0 0 10 10"><circle cx="5" cy="5" r="4.3" fill="none" stroke="var(--white)" stroke-width="1.1"/><ellipse cx="5" cy="5" rx="1.9" ry="4.3" fill="none" stroke="var(--white)" stroke-width="0.9"/><path d="M0.8 5 H9.2" stroke="var(--white)" stroke-width="0.9"/></svg>
      www.gralotund.com
    </p>
  </div>
</section>

</body>
</html>
```